Business Card Design for Property Development Company Director

I am looking for a professional and unforgettable business card design for our Director of our Property Development Company.
Please see attached .pptx file to find out what information to include. You don't have to follow the exact format shown in the file - I am interested to see your creative flair using the information provided.

```html
<!DOCTYPE html>
<html lang="en">
<head>
<meta charset="utf-8">
<title>Halvorne Property Group – Business Card</title>
<link href="https://fonts.googleapis.com/css2?family=Roboto:wght@400;500;700&display=swap" rel="stylesheet">
<style>
  :root {
    --page-bg: #d9d9db;
    --card-dark: #1f1f20;
    --card-light: #ffffff;
    --brand-blue: #1259a8;
    --brand-grey: #5a5a5c;
    --muted-grey: #6e6e70;
    --ink: #111111;
  }
  * { box-sizing: border-box; margin: 0; padding: 0; }
  html, body {
    width: 1200px; height: 1200px; overflow: hidden;
    background: var(--page-bg);
    font-family: "Roboto", Arial, sans-serif;
  }
  .sheet {
    width: 1200px; height: 1200px;
    display: flex; flex-direction: column; align-items: center; justify-content: center;
    gap: 60px;
  }
  .card {
    width: 860px; height: 490px;
    border-radius: 28px;
    position: relative; overflow: hidden;
  }
  .card--back { background: var(--card-dark); }
  .card--front { background: var(--card-light); }

  .wordmark {
    display: flex; align-items: center; gap: 18px;
    color: var(--brand-blue); font-weight: 700;
  }
  .wordmark__square {
    width: 64px; height: 64px; background: var(--brand-blue); flex: none;
  }
  .wordmark__name {
    font-size: 46px; line-height: 1.05; letter-spacing: 1px; text-transform: uppercase;
  }
  .wordmark__name small { display: block; font-size: 22px; letter-spacing: 7px; }

  /* back */
  .back__tagline {
    position: absolute; top: 70px; left: 0; right: 0; text-align: center;
    color: var(--brand-blue); font-weight: 500; font-size: 26px; line-height: 1.2;
  }
  .back__logo {
    position: absolute; top: 175px; left: 0; right: 0; display: flex; justify-content: center;
  }
  .back__cta {
    position: absolute; bottom: 62px; left: 0; right: 0; text-align: center;
    color: var(--muted-grey); font-size: 22px;
  }
  .back__cta strong { color: var(--brand-blue); font-weight: 400; }

  /* front */
  .front__logo {
    position: absolute; top: 90px; left: 0; right: 0; display: flex; justify-content: center;
  }
  .front__details {
    position: absolute; top: 262px; left: 0; right: 0;
    display: flex; justify-content: center; align-items: stretch; gap: 28px;
  }
  .person { text-align: right; padding-top: 6px; }
  .person__name { color: var(--brand-blue); font-weight: 700; font-size: 32px; }
  .person__role { color: var(--ink); font-size: 21px; margin-top: 2px; }
  .divider { width: 2px; background: var(--brand-blue); }
  .contacts { list-style: none; color: var(--ink); font-size: 22px; }
  .contacts li { display: flex; align-items: center; gap: 12px; height: 34px; }
  .contacts svg { width: 20px; height: 20px; flex: none; }
  .front__band {
    position: absolute; left: 0; right: 0; bottom: 0; height: 92px;
    background: var(--brand-blue); color: #fff;
    display: flex; align-items: center; justify-content: center;
    font-size: 24px; font-weight: 500;
  }
</style>
</head>
<body>
<main class="sheet">
  <section class="card card--back">
    <p class="back__tagline">Property Development<br>&amp; Site Acquisition Specialists</p>
    <div class="back__logo">
      <div class="wordmark">
        <span class="wordmark__square"></span>
        <span class="wordmark__name">Halvorne<small>Property Group</small></span>
      </div>
    </div>
    <p class="back__cta">Ask me about our <strong>INVESTMENT &amp; PARTNERSHIP</strong> opportunities</p>
  </section>

  <section class="card card--front">
    <div class="front__logo">
      <div class="wordmark">
        <span class="wordmark__square"></span>
        <span class="wordmark__name">Halvorne<small>Property Group</small></span>
      </div>
    </div>
    <div class="front__details">
      <div class="person">
        <p class="person__name">Daniel Mercer</p>
        <p class="person__role">Director</p>
      </div>
      <span class="divider"></span>
      <ul class="contacts">
        <li>
          <svg viewBox="0 0 24 24" fill="#1259a8"><path d="M6.6 10.8a15 15 0 0 0 6.6 6.6l2.2-2.2a1 1 0 0 1 1-.25 11.4 11.4 0 0 0 3.6.57 1 1 0 0 1 1 1V20a1 1 0 0 1-1 1A17 17 0 0 1 3 4a1 1 0 0 1 1-1h3.5a1 1 0 0 1 1 1c0 1.25.2 2.45.57 3.6a1 1 0 0 1-.25 1z"/></svg>
          0400 218 736
        </li>
        <li>
          <svg viewBox="0 0 24 24" fill="none" stroke="#1259a8" stroke-width="2"><rect x="3" y="5" width="18" height="14" rx="1"/><path d="M3 6l9 7 9-7"/></svg>
          daniel@halvorne.com.au
        </li>
        <li>
          <svg viewBox="0 0 24 24" fill="none" stroke="#1259a8" stroke-width="1.8"><circle cx="12" cy="12" r="9"/><path d="M3 12h18M12 3c3 3 3 15 0 18M12 3c-3 3-3 15 0 18"/></svg>
          www.halvorne.com.au
        </li>
      </ul>
    </div>
    <div class="front__band">Real Estate Lic: 5129036 &amp; 5129037</div>
  </section>
</main>
</body>
</html>
```